Automotive Accessories Business Card

Design a business template that match our new logo design and our industry.

https://www.qelmotorgear.com/

Target Market(s)

Aftermarket auto parts and accessories

Industry/Entity Type

automotive

Contact Information for Business Card

company logo

Font styles to use
Serif
Sans Serif

Colors
EB3D1F
EC4F4E
F09395
F8D3D4
FCEDEE

```html
<!DOCTYPE html>
<html lang="en">
<head>
<meta charset="utf-8">
<title>QEL Motor Gear – Business Card</title>
<link rel="stylesheet" href="https://fonts.googleapis.com/css2?family=Open+Sans:ital,wght@0,400;0,700;0,800;1,700&display=swap">
<style>
  :root {
    --page: #e9e7e5;
    --card-white: #f7f7f7;
    --card-dark: #3a3a3a;
    --card-dark-deep: #2a2a2a;
    --ink: #3b3b3d;
    --ink-soft: #555558;
    --brand-red: #e0323a;
    --divider-grey: #6c6c6e;
  }
  * { box-sizing: border-box; margin: 0; padding: 0; }
  html, body {
    width: 1200px; height: 960px; overflow: hidden;
    background: var(--page);
    font-family: "Open Sans", Arial, sans-serif;
    color: var(--ink);
  }
  .sheet {
    width: 1200px; height: 960px;
    display: flex; flex-direction: column; align-items: center; justify-content: center;
    gap: 40px;
  }
  .card {
    width: 700px; height: 400px;
    position: relative;
    box-shadow: 0 6px 18px rgba(0,0,0,.18);
    overflow: hidden;
  }

  /* Front */
  .card--front {
    background: linear-gradient(160deg, #ffffff 0%, var(--card-white) 60%, #ececec 100%);
    display: flex; align-items: center;
  }
  .brand {
    width: 330px; padding-left: 60px;
    display: flex; align-items: center; gap: 12px;
  }
  .brand__mark { width: 22px; height: 22px; background: var(--brand-red); flex: none; }
  .brand__name {
    font-weight: 800; font-size: 34px; line-height: 1.05;
    color: var(--brand-red); letter-spacing: .5px;
  }
  .divider {
    width: 2px; height: 190px; flex: none;
    background: linear-gradient(to bottom, var(--brand-red) 0 40%, transparent 40% 48%, var(--divider-grey) 48% 100%);
  }
  .contact { padding-left: 34px; }
  .contact__name {
    font-weight: 800; font-size: 30px; letter-spacing: 2px;
    text-transform: uppercase; color: var(--ink); line-height: 1.1;
  }
  .contact__title { font-size: 18px; color: var(--ink-soft); margin-bottom: 18px; }
  .contact__list { list-style: none; }
  .contact__item {
    display: flex; align-items: center; gap: 12px;
    font-size: 18px; color: var(--ink); line-height: 1.55;
  }
  .contact__icon { width: 18px; height: 18px; flex: none; fill: var(--brand-red); }
  .contact__domain { color: var(--brand-red); font-weight: 700; font-style: italic; }

  /* Back */
  .card--back {
    display: flex; align-items: center; justify-content: center;
  }
  .back__texture {
    position: absolute; inset: 0;
    background: radial-gradient(ellipse at 40% 40%, #4a4a4a 0%, var(--card-dark) 55%, var(--card-dark-deep) 100%);
  }
  .back__brand {
    position: relative; display: flex; align-items: center; gap: 14px;
  }
  .back__brand .brand__mark { width: 26px; height: 26px; background: #ffffff; }
  .back__brand .brand__name { color: #ffffff; font-size: 46px; }
</style>
</head>
<body>
<main class="sheet">
  <section class="card card--front">
    <div class="brand">
      <span class="brand__mark"></span>
      <span class="brand__name">QEL Motor Gear</span>
    </div>
    <div class="divider"></div>
    <div class="contact">
      <h1 class="contact__name">Dana Reyes</h1>
      <p class="contact__title">Sales Manager</p>
      <ul class="contact__list">
        <li class="contact__item">
          <svg class="contact__icon" viewBox="0 0 24 24" aria-hidden="true"><path d="M6.6 10.8a15.1 15.1 0 0 0 6.6 6.6l2.2-2.2a1 1 0 0 1 1-.25 11.4 11.4 0 0 0 3.6.57 1 1 0 0 1 1 1V20a1 1 0 0 1-1 1A17 17 0 0 1 3 4a1 1 0 0 1 1-1h3.5a1 1 0 0 1 1 1c0 1.25.2 2.45.57 3.57a1 1 0 0 1-.25 1z"/></svg>
          1-800-555-0147
        </li>
        <li class="contact__item">
          <svg class="contact__icon" viewBox="0 0 24 24" aria-hidden="true"><path d="M2 5h20v14H2z M3.5 6.5 12 13l8.5-6.5" fill="none" stroke="#e0323a" stroke-width="2"/><path d="M2 5h20l-10 8z"/></svg>
          sales@qelmotorgear.com
        </li>
        <li class="contact__item">
          <svg class="contact__icon" viewBox="0 0 24 24" aria-hidden="true"><circle cx="12" cy="12" r="10"/><path d="M2 12h20M12 2c3 3 3 17 0 20M12 2c-3 3-3 17 0 20M4.5 7h15M4.5 17h15" fill="none" stroke="#fff" stroke-width="1.4"/></svg>
          <span>www.<span class="contact__domain">qelmotorgear</span>.com</span>
        </li>
      </ul>
    </div>
  </section>

  <section class="card card--back">
    <div class="back__texture" role="img" aria-label="Dark tiled pattern background"></div>
    <div class="back__brand">
      <span class="brand__mark"></span>
      <span class="brand__name">QEL Motor Gear</span>
    </div>
  </section>
</main>
</body>
</html>
```